VOMRA Pty Ltd Business Card

Looking for a simple yet eye-catching double-sided business card design using my company logo on one side and contact details on the other.

Target Market(s)

Government

Industry/Entity Type

Communication Systems Engineering

Contact Information for Business Card

VOMRA Pty Ltd

Requirements
Nice to have
• Would be great to have a QR code so details can be scanned into contacts

```html
<!DOCTYPE html>
<html lang="en">
<head>
<meta charset="utf-8">
<title>VOMRA Pty Ltd Business Card</title>
<link rel="stylesheet" href="https://fonts.googleapis.com/css2?family=Montserrat:wght@400;500;800&display=swap">
<style>
  :root {
    --slate: #37424a;
    --ink: #0a0a0a;
    --paper: #ffffff;
    --backdrop: #e6e8ea;
    --text: #2f3a42;
  }
  * { box-sizing: border-box; margin: 0; padding: 0; }
  html, body {
    width: 1200px; height: 960px; overflow: hidden;
    background: var(--backdrop);
    font-family: "Montserrat", Arial, sans-serif;
  }
  .sheet {
    width: 1200px; height: 960px;
    display: flex; flex-direction: column;
    align-items: center; justify-content: center; gap: 50px;
  }
  .card {
    position: relative;
    width: 700px; height: 400px;
    border-radius: 34px;
    overflow: hidden;
    box-shadow: 0 10px 28px rgba(0,0,0,0.18);
  }
  /* Front */
  .card-front {
    background: var(--slate);
    display: flex; align-items: center; justify-content: center; gap: 26px;
  }
  .brand-dot {
    width: 74px; height: 74px; border-radius: 50%;
    background: var(--paper);
  }
  .brand-name {
    color: var(--paper);
    font-weight: 800; font-size: 104px; letter-spacing: 4px; line-height: 1;
  }
  /* Back */
  .card-back { background: var(--paper); }
  .card-back .wave { position: absolute; inset: 0; width: 700px; height: 400px; }
  .back-brand {
    position: absolute; left: 52px; top: 150px;
    display: flex; align-items: center; gap: 14px;
  }
  .back-brand .brand-dot { width: 46px; height: 46px; background: var(--slate); }
  .back-brand .brand-name { color: var(--slate); font-size: 52px; letter-spacing: 1px; }
  .divider {
    position: absolute; left: 372px; top: 28px;
    width: 2px; height: 200px; background: var(--slate);
  }
  .contact {
    position: absolute; left: 394px; top: 28px;
    color: var(--text);
  }
  .person-name { font-weight: 800; font-size: 25px; letter-spacing: 0.5px; line-height: 1.1; }
  .person-role { font-weight: 400; font-size: 15px; margin-top: 3px; }
  .contact-list { list-style: none; margin-top: 16px; }
  .contact-list li {
    display: flex; align-items: center; gap: 9px;
    font-size: 15px; line-height: 1.45;
  }
  .contact-list svg { width: 14px; height: 14px; flex: none; fill: var(--slate); }
  .address { font-size: 15px; line-height: 1.3; margin-top: 12px; }
</style>
</head>
<body>
<main class="sheet">
  <section class="card card-front" aria-label="Card front">
    <span class="brand-dot"></span>
    <span class="brand-name">VOMRA</span>
  </section>

  <section class="card card-back" aria-label="Card back">
    <svg class="wave" viewBox="0 0 700 400" aria-hidden="true">
      <path d="M0,352 C230,346 420,320 515,276 C450,330 270,370 0,376 Z" fill="var(--ink)"/>
      <path d="M0,386 C250,376 430,340 520,292 C580,260 630,250 700,246 L700,400 L0,400 Z" fill="var(--slate)"/>
    </svg>

    <div class="back-brand">
      <span class="brand-dot"></span>
      <span class="brand-name">VOMRA</span>
    </div>

    <span class="divider"></span>

    <div class="contact">
      <p class="person-name">DANIEL HART</p>
      <p class="person-role">Managing Director</p>
      <ul class="contact-list">
        <li><svg viewBox="0 0 24 24"><path d="M6.6 10.8a15.1 15.1 0 0 0 6.6 6.6l2.2-2.2a1 1 0 0 1 1-.25 11.4 11.4 0 0 0 3.6.57 1 1 0 0 1 1 1V20a1 1 0 0 1-1 1A17 17 0 0 1 3 4a1 1 0 0 1 1-1h3.5a1 1 0 0 1 1 1c0 1.25.2 2.45.57 3.57a1 1 0 0 1-.25 1z"/></svg>02 5550 1847</li>
        <li><svg viewBox="0 0 24 24"><path d="M2 5h20v2l-10 6L2 7z M2 9l10 6 10-6v10H2z"/></svg>admin@vomra.com.au</li>
        <li><svg viewBox="0 0 24 24"><circle cx="12" cy="12" r="10"/></svg>www.vomra.com.au</li>
      </ul>
      <p class="address">14-16 Wattle Lane Redfern<br>NSW 2016 Australia</p>
    </div>
  </section>
</main>
</body>
</html>
```